Valdane Companies Business Card Design

We need a new business card for our Private Equity Real Estate Development firm, “Valdane” and our EB-5 regional center “Thornmere Regional Center” on one card. We prefer a design that is simple, elegant, and represents the luxury products we design and build as well as the financial security and stability our successful history has produced. We are an industry leader in our field and 3rd generation family business that has evolved into an institutional quality investment platform. Considered design size is standard business card dimensions (3.5 x 2 inches with an additional 1/8 inch space for design elements or backgrounds that extend beyond the finished size of your piece.

Target Market(s)

• High net worth individuals
• Highly skilled technical workers and physicians in the US seeking investment-based immigration opportunities
• Sophisticated private equity investors
• Intermediary partners include domestic attorneys and investment brokers, as well as international agent networks
• US real estate developers

Industry/Entity Type

Finance

Contact Information for Business Card

(Providing placeholder info for personal information, please design for longer character spaces, longer names and addresses etc..)
• Logo for Valdane
• Logo for Thornmere Regional Center
• Full name: Marcus Valdane
• Job title: CEO
• Email address: mvaldane@valdanecompanies.com
• Cell phone number: +1.555.314.2287
• Office number +1.555.628.4410
• Office address: Larkfield Court 5, 4817 Vista Orilla, Ashford Hills, CA.
• Website: www.valdanecompanies.com

Font styles to use
Serif
Sans Serif

Colors
ec1f27
ffffff
000000

Requirements
Must have
• • Logo for Valdane
• • Logo for Thornmere Regional Center
• - Use rounded corners
• (See .ai file included for logos)
Nice to have
• • Simple, elegant design
• • Aesthetically compatible with our website design (www.valdanecompanies.com)
• • Color palette including but not limited to white, black, and red (as per logos)
Should not have
• - Not too much red color
• - Do not stack both logos on top of each other

```html
<!DOCTYPE html>
<html lang="en">
<head>
<meta charset="utf-8">
<title>Valdane Companies Business Card</title>
<link rel="stylesheet" href="https://fonts.googleapis.com/css2?family=Playfair+Display:wght@700&family=Tinos:wght@400;700&family=Montserrat:wght@400&display=swap">
<style>
  :root {
    --page: #141416;
    --card: #202123;
    --card-edge: #2a2b2e;
    --silver: #e6e6e8;
    --muted: #9a9b9f;
    --rule: #8c8d91;
    --map: #2c2d30;
  }
  * { box-sizing: border-box; margin: 0; padding: 0; }
  html, body { width: 1200px; height: 800px; overflow: hidden; background: var(--page); }
  .canvas { position: relative; width: 1200px; height: 800px; }

  .card {
    position: absolute;
    width: 560px;
    height: 320px;
    border-radius: 22px;
    background: var(--card);
    box-shadow: 0 0 0 1px var(--card-edge);
    overflow: hidden;
  }
  .card--front { left: 30px; top: 120px; }
  .card--back { left: 610px; top: 360px; }

  .world-map {
    position: absolute;
    left: 90px; top: 40px;
    width: 440px; height: 240px;
    border-radius: 40px;
    background: radial-gradient(ellipse at 50% 50%, var(--map) 0%, rgba(44,45,48,0.4) 55%, rgba(32,33,35,0) 80%);
  }

  .brand {
    position: absolute;
    display: flex;
    align-items: center;
    gap: 14px;
    color: var(--silver);
  }
  .brand__mark {
    width: 14px; height: 14px;
    background: var(--silver);
  }
  .brand__divider { width: 1px; height: 54px; background: var(--rule); }
  .brand__name {
    font-family: "Playfair Display", Georgia, serif;
    font-weight: 700;
    font-size: 44px;
    letter-spacing: 1px;
    line-height: 1;
  }
  .brand__tagline {
    font-family: "Montserrat", Arial, sans-serif;
    font-size: 11px;
    letter-spacing: 7px;
    color: var(--muted);
    margin-top: 6px;
  }
  .card--front .brand { left: 110px; top: 128px; }
  .card--back .brand { left: 40px; top: 110px; }
  .card--back .brand__name { font-size: 38px; }
  .card--back .brand__tagline { font-size: 9px; letter-spacing: 5px; }

  .divider-line {
    position: absolute;
    left: 370px; top: 144px;
    width: 166px; height: 1px;
    background: var(--rule);
  }

  .address {
    position: absolute;
    right: 26px; top: 28px;
    text-align: right;
    font-family: "Tinos", "Times New Roman", serif;
    font-style: normal;
    font-size: 13px;
    line-height: 1.35;
    color: var(--silver);
  }

  .person {
    position: absolute;
    left: 40px; top: 200px;
    color: var(--silver);
    font-family: "Tinos", "Times New Roman", serif;
  }
  .person__row { display: flex; align-items: center; gap: 12px; }
  .person__name { font-weight: 700; font-size: 19px; }
  .person__rule { width: 110px; height: 1px; background: var(--rule); }
  .person__title { font-size: 14px; margin-top: 1px; }

  .contacts {
    list-style: none;
    margin-top: 8px;
    font-size: 13px;
    line-height: 1.4;
  }
  .contacts li { display: flex; align-items: center; gap: 7px; }
  .contacts svg { width: 11px; height: 11px; fill: none; stroke: var(--silver); stroke-width: 1.4; }
</style>
</head>
<body>
<main class="canvas">

  <section class="card card--front" aria-label="Card front">
    <div class="world-map" role="img" aria-label="Faint world map background"></div>
    <div class="brand">
      <span class="brand__mark"></span>
      <span class="brand__divider"></span>
      <div>
        <div class="brand__name">VALDANE</div>
        <div class="brand__tagline">CAPITAL</div>
      </div>
    </div>
  </section>

  <section class="card card--back" aria-label="Card back">
    <address class="address">
      Larkfield Court 5<br>
      4817 Vista Orilla<br>
      Ashford Hills, CA.
    </address>

    <div class="brand">
      <span class="brand__mark"></span>
      <span class="brand__divider"></span>
      <div>
        <div class="brand__name">THORNMERE</div>
        <div class="brand__tagline">REGIONAL CENTER</div>
      </div>
    </div>
    <span class="divider-line"></span>

    <div class="person">
      <div class="person__row">
        <span class="person__name">Marcus Valdane</span>
        <span class="person__rule"></span>
      </div>
      <div class="person__title">CEO</div>
      <ul class="contacts">
        <li>
          <svg viewBox="0 0 12 12"><rect x="3" y="1" width="6" height="10" rx="1"/></svg>
          +1.555.314.2287
        </li>
        <li>
          <svg viewBox="0 0 12 12"><path d="M2 5 Q6 1 10 5 L9 6 L7 5 L5 5 L3 6 Z"/><rect x="3" y="6" width="6" height="4"/></svg>
          +1.555.628.4410
        </li>
        <li>
          <svg viewBox="0 0 12 12"><rect x="1" y="3" width="10" height="7"/><path d="M1 3 L6 7 L11 3"/></svg>
          mvaldane@valdanecompanies.com
        </li>
      </ul>
    </div>
  </section>

</main>
</body>
</html>
```